Church Website with Home Page and Member Sermon Library

I am in need of an updated design for our church website. This will include 4 pages (outlined below). We are a conservative, evangelical, Christian church. The site should be modern and clean, while still reflecting our conservative values. I already have a logo for our church, and I want the site to incorporate the logo, and match the logo/branding. Stock photos are allowed if needed, but I have uploaded some images of our church and would prefer those images to be used if possible. Any stock photos used should not include any people in the photos (scenery, nature, buildings, animals, etc. are fine).

The site will need 4 pages: Home, Support Us (Donate), Login, and Recording Library.

Page 1: Home
The home page should include the following sections:

- Navigation: Should include links to each section of the home page plus a "listen live" link which will take the user to a live-streaming site and a "support us" link which will take the user to a support/donate page.

- Announcements: Can be either a banner or some other design, but there needs to be some way for us to post announcements for visitors to see. I'm open for creative ideas in this section, but would like it not to take up a lot of room on the page.

- About Us: Should include address, service times (see attached document), and information about the church.

- Pastor Bio: A section that introduces our pastor and gives a short bio about our pastor. Would like this section to include a picture of our pastor. Somewhere in this section I would like to include this Bible reference: "And I will give you pastors according to mine heart, which shall feed you with knowledge and understanding. Jer 3:15 LPW"

- Articles of Faith (What We Believe): This should include several sub-sections each with a heading, body, and possibly 1 or more scripture references. I have attached a document to the brief that includes our articles of faith. Feel free to be creative with this section in how you lay these out and format them.

- Support Us: A small section that explains what kind of support someone can give and a link to a donation page. The link can say something like "Support Us" or "Donate Now".

- Contact form: A contact form that allows the visitor to send us a message. The contact form should ask for name, email, phone, and message.

- Footer: A footer that will be displayed on all pages of the site. This should include at a minimum a link to the home page (or a link to each individual section in the home page if you prefer), a link to "listen live", a link to "support us", a link to "contact us" (or you can put the contact form directly in the footer if you prefer), the address, and a "member login" link.

Page 2: Support Us
The donation page should include a form the visitor can fill out to make a donation. We will embed a third party form later. For this design, please just mock out the design with a basic form asking for name, phone, and email.

Page 3: Login
The recording library (detailed below) will require members to login with a shared numeric code before accessing the page. We need a design for a login screen. The screen should include navigation/footer just like all other pages, but the body of the login page will consist only of a form that asks the user to enter the access code and then a "login" button.

Page 4: Recording Library

The library page is a member-only page that will require a shared, numeric pass code to access. On this page, members will be able to access a filterable list of past sermons. The page by default should display most recent sermons, but should also include a search form that allows the member to filter the sermon list to find a particular sermon. The search form should allow the user to select a filter type (e.g. Speaker name, date, event, etc.) and type in a value to search. They should be able to add multiple filters and remove filters that have been added. Each sermon that is displayed in the result list should include basic information such as title, date, speaker, tags, etc. along with a download icon, and an embedded audio player where they can click a play button to stream it on-demand. Each sermon should also have clickable tags associated with it that can be used to find related sermons.
Updates

I have uploaded several images of our church. Feel free to incorporate these into your design if possible.

Target Market(s)

Church Members

Industry/Entity Type

Religion

Number of Pages Required

4 page

Font styles to use
Sans Serif

Colors

Designer to choose colors to be used in the design.

Requirements
Must have
• Must incorporate the logo (attached)
Nice to have
• Would like the design to incorporate pictures of our church (attached) instead of stock photos if possible.
Should not have
• Please avoid an overly cluttered design. Stock photos used should not include any people in the photos.

```html
<!DOCTYPE html>
<html lang="en">
<head>
<meta charset="utf-8">
<title>Grace Covenant Church</title>
<link href="https://fonts.googleapis.com/css2?family=Cinzel:wght@400;500&family=Montserrat:ital,wght@0,400;0,500;0,600;1,400&display=swap" rel="stylesheet">
<style>
:root{
  --ink:#232323;
  --text:#5a5a5a;
  --accent:#2aa8c8;
  --green:#7ea86a;
  --frame:#4b6a86;
  --frame-light:#9fb1c2;
  --panel:#f4f4f4;
  --footer:#333333;
  --field:#3d3d3d;
  --alert:#e0141b;
}
*{box-sizing:border-box;margin:0;padding:0}
html,body{width:1200px;height:3979px;overflow:hidden;background:#fff}
body{font-family:"Montserrat",sans-serif;color:var(--text)}
.page{position:relative;width:1200px;height:3979px;overflow:hidden}
.abs{position:absolute}
.serif{font-family:"Cinzel",serif;font-weight:400;color:var(--ink)}
.brand{position:absolute;text-align:center;font-family:"Cinzel",serif;font-weight:400;color:var(--green);line-height:1.15;letter-spacing:3px}

.hero-photo{left:0;top:0;width:1200px;height:584px;
  background:linear-gradient(90deg,#ffffff 0%,rgba(255,255,255,.6) 10%,rgba(255,255,255,0) 25%),
  linear-gradient(180deg,#fbfaf6 0%,#f2ede0 45%,#e8dcc3 72%,#b98c5c 88%,#9c6b3f 100%)}
.nav{top:66px;left:430px;font-size:13px}
.nav a{color:#444;text-decoration:none;position:absolute;white-space:nowrap}
.btn{position:absolute;background:var(--green);color:#fff;font-family:"Cinzel",serif;font-size:14px;display:flex;align-items:center;justify-content:center;letter-spacing:.5px}
.hero-title{left:0;width:1200px;top:272px;text-align:center;font-size:56px;letter-spacing:6px}
.hero-rule{left:560px;top:337px;width:80px;height:2px;background:#222}
.hero-sub{left:300px;width:600px;top:372px;text-align:center;font-size:15px;line-height:23px;color:#333}

.about-photo{left:159px;top:648px;width:317px;height:521px;border-radius:50% 50% 0 0/32% 32% 0 0;
  background:linear-gradient(180deg,#c9b9a1 0%,#efe9df 40%,#e7ddcf 70%,#a87a4e 100%)}
.eyebrow{font-family:"Cinzel",serif;font-size:14px;letter-spacing:1px;color:#333}
.h2{font-family:"Cinzel",serif;font-weight:400;color:var(--ink);font-size:36px;line-height:41px;letter-spacing:3px}
.para{font-size:13px;line-height:22px;color:var(--text)}
.accent-rule{height:3px;background:var(--accent)}
.times{left:573px;top:1048px;list-style:none;font-family:"Cinzel",serif;font-size:13px;color:#333}
.times li{position:absolute;white-space:nowrap;left:0}
.times .num{color:var(--accent);margin-right:8px}
.times b{font-weight:500;color:#111}
.address{left:573px;top:1148px;font-size:12px;color:var(--text)}
.address span{font-family:"Cinzel",serif;color:#333;margin-right:8px}

.ann-frame{left:178px;top:1270px;width:844px;height:304px;background:var(--panel);border:5px solid var(--frame);outline:2px solid var(--frame-light);outline-offset:-14px}
.ann-brand{left:530px;top:1232px;width:140px;font-size:13px;letter-spacing:2px}
.ann-title{left:178px;width:844px;top:1356px;text-align:center;font-size:36px;letter-spacing:3px}
.ann-text{left:320px;width:560px;top:1405px;text-align:center;font-size:13px;line-height:22px;color:#333}
.ann-left{right:628px;top:1475px;text-align:right}
.ann-right{left:616px;top:1472px}
.ann-div{left:592px;top:1470px;width:1px;height:58px;background:#555}

.pastor-photo{left:616px;top:1672px;width:406px;height:419px;background:linear-gradient(180deg,#cfc7b8 0%,#b9ad9a 45%,#3a3a3a 75%,#2a2a2a 100%)}
.link-green{font-family:"Cinzel",serif;font-size:14px;color:var(--green);border-bottom:1px solid var(--green);padding-bottom:4px}
.quote{left:139px;top:2116px;width:380px;font-size:12px;line-height:19px;font-style:italic;color:#555;border-left:3px solid var(--accent);padding-left:12px}

.articles-bg{left:0;top:2217px;width:1200px;height:865px;
  background:radial-gradient(ellipse at 50% 45%,#f7f7f7 0%,#eeeeee 55%,#e4e4e4 100%)}
.art-title{left:0;width:1200px;top:2310px;text-align:center;font-size:36px;letter-spacing:3px}
.art{position:absolute;width:240px}
.art h3{font-family:"Cinzel",serif;font-weight:400;font-size:17px;letter-spacing:1.5px;color:#222;padding-left:16px;position:relative;line-height:22px;margin-bottom:12px}
.art h3::before{content:"";position:absolute;left:0;top:9px;width:5px;height:5px;border-radius:50%;background:var(--accent)}
.art p{font-size:12px;line-height:20px;color:#666;margin-bottom:10px}
.art ol{list-style:none;font-size:10px;color:#444;line-height:23px}
.art ol span{font-family:"Cinzel",serif;color:var(--green);font-size:12px;margin-right:8px}
.art-div{position:absolute;height:1px;background:#d8d8d8;width:215px}

.footer{left:0;width:1200px;background:var(--footer)}
.f-title{font-family:"Cinzel",serif;font-size:18px;letter-spacing:2px;color:#e6e6e6}
.field{position:absolute;background:var(--field);border:1px solid #5e5e5e;color:#bbb;font-size:12px;padding:9px 12px}
.f-text{font-size:12px;line-height:19px;color:#bdbdbd}
.copy{font-size:11px;color:#d0d0d0}
.social{display:flex;gap:14px}
.social span{width:10px;height:10px;border-radius:50%;background:#e0e0e0;display:block}
.uline{position:absolute;border-bottom:1px solid #8c8c8c;font-size:11px;color:#cfcfcf;padding-bottom:8px;display:flex;justify-content:space-between}
.variant{left:181px;top:3504px;font-family:"Cinzel",serif;font-weight:500;font-size:30px;color:var(--alert);letter-spacing:2px}
</style>
</head>
<body>
<div class="page">

  <div class="abs hero-photo" role="img" aria-label="Bright church interior with white arches, stained glass windows, wooden pews and a red carpeted aisle"></div>
  <div class="brand" style="left:139px;top:60px;width:140px;font-size:17px;letter-spacing:2px">GRACE<br>COVENANT</div>
  <nav class="abs nav">
    <a style="left:0;top:0">Home</a>
    <a style="left:72px;top:0">About</a>
    <a style="left:146px;top:0">Our Pastor</a>
    <a style="left:250px;top:0">Articles Of Faith</a>
    <a style="left:382px;top:0">Listen Live</a>
  </nav>
  <div class="btn" style="left:929px;top:57px;width:99px;height:36px">DONATE</div>
  <h1 class="abs serif hero-title">KEEP FAITH ALWAYS</h1>
  <div class="abs hero-rule"></div>
  <p class="abs hero-sub">Lorem ipsum dolor sit amet consectetur cursus egestas turpis turpis enim et amet sed magna.</p>

  <div class="abs about-photo" role="img" aria-label="Tall vaulted church nave with rows of wooden chairs"></div>
  <div class="abs eyebrow" style="left:573px;top:659px">ABOUT</div>
  <h2 class="abs h2" style="left:573px;top:687px;width:420px">WELCOME TO GRACE COVENANT CHURCH</h2>
  <p class="abs para" style="left:573px;top:815px;width:450px">Ut diam tortor consectetur lacus scelerisque tortor congue viverra egestas. Tristique in consectetur leo arcu blandit diam et sed volutpat.</p>
  <p class="abs para" style="left:573px;top:895px;width:450px">Aliquam at commodo venenatis quis. Velit neque interdum molestie risus consectetur vestibulum a eget. Ultricies volutpat orci eros quisque ullamcorper quis est.</p>
  <div class="abs accent-rule" style="left:573px;top:980px;width:152px"></div>
  <div class="abs eyebrow" style="left:573px;top:1011px">SERVICE TIME ARE</div>
  <ul class="abs times">
    <li style="top:2px"><span class="num">01.</span>TRADITIONAL WORSHIP SERVICES: <b>09:00 AM - 11:05 AM</b></li>
    <li style="top:37px"><span class="num">02.</span>TRADITIONAL WORSHIP SERVICES: <b>09:00 AM - 11:05 AM</b></li>
    <li style="top:74px"><span class="num">03.</span>TRADITIONAL WORSHIP SERVICES: <b>09:00 AM - 11:05 AM</b></li>
  </ul>
  <p class="abs address"><span>ADDRESS:</span>1420 Meadow Lane, Brookfield, OH 44403</p>

  <div class="abs ann-frame"></div>
  <div class="brand ann-brand">GRACE<br>COVENANT</div>
  <h2 class="abs serif ann-title">ANNOUNCEMENT BANNER SPOT</h2>
  <p class="abs ann-text">Ullamcorper facilisi egestas semper fames suscipit penatibus amet. Ut diam tortor consectetur lacus scelerisque tortor congue viverra</p>
  <div class="abs ann-left">
    <div class="serif" style="font-size:19px;letter-spacing:2px">ANNOUNCEMENT</div>
    <div class="serif" style="font-size:11px;color:#444;margin-top:8px;letter-spacing:1px">FABRUARY 16TH</div>
  </div>
  <div class="abs ann-div"></div>
  <div class="abs ann-right">
    <div class="serif" style="font-size:13px;line-height:15px;letter-spacing:1.5px;color:#333">GRACE COVENANT<br>CHURCH</div>
    <div style="font-size:12px;font-style:italic;color:#333;margin-top:6px">Pastor Samuel Reed</div>
  </div>

  <div class="abs eyebrow" style="left:139px;top:1698px">OUR PASTOR</div>
  <h2 class="abs h2" style="left:139px;top:1720px;width:400px">A MAN OF PRAYER AND HIGH SPIRITUALITY</h2>
  <div class="abs accent-rule" style="left:139px;top:1857px;width:122px"></div>
  <p class="abs para" style="left:139px;top:1888px;width:375px">Ullamcorper facilisi egestas semper fames suscipit penatibus amet. Ut diam tortor consectetur lacus scelerisque tortor congue viverra egestas. Tristique in consectetur leo arcu blandit diam et sed volutpat.</p>
  <p class="abs para" style="left:139px;top:1992px;width:375px">Aliquam at commodo venenatis quis. Velit neque interdum molestie risus consectetur vestibulum a eget.</p>
  <div class="abs link-green" style="left:139px;top:2074px">READ FULL BIO</div>
  <blockquote class="abs quote">“And I will give you pastors according to mine heart, which shall feed you with knowledge and understanding.” Jer 3:15 LPW</blockquote>
  <div class="abs pastor-photo" role="img" aria-label="Portrait of the pastor in a dark clerical shirt holding a Bible"></div>
  <div class="abs serif" style="left:616px;top:2106px;font-size:21px;letter-spacing:1px;font-weight:500">DANIEL WHITFORD</div>

  <div class="abs articles-bg" role="img" aria-label="Softly blurred church interior with pews in pale grey tones"></div>
  <h2 class="abs serif art-title">ARTICLES OF FAITH</h2>
  <div class="abs accent-rule" style="left:527px;top:2362px;width:146px"></div>

  <div class="art" style="left:184px;top:2413px">
    <h3>THE GOD HEAD.</h3>
    <p>We believe in the God head bodily, known as the Divine Trinity. This body consist of God the father, Jesus Christ, his only begotten son and the redeemer of the world, and of the Holy Ghost, The third person of the Divine Trinity</p>
  </div>
  <div class="art-div" style="left:184px;top:2612px"></div>
  <div class="art" style="left:184px;top:2680px">
    <h3>BAPTISM OF THE HOLY GHOST.</h3>
    <p>We believe in the baptism of the Holy Ghost as it is taught in the Bible and promised by our Lord Jesus Christ, with speaking in tongues as the Spirit gives utterance as the initial evidence. Acts 2:4 we believe that the gift of the Holy Ghost is for all believers as the Lord promised. Acts 2:17-18</p>
  </div>
  <div class="art-div" style="left:184px;top:2916px"></div>

  <div class="art" style="left:479px;top:2413px">
    <h3>FULL SALVATION.</h3>
    <p>We believe that Salvation is received only when a person comes to the realization that he or she is lost and separated from God and becomes full of godly sorrow, confessing their sins and true repentance, believing in the shed blood of the Lord Jesus Christ as the only sacrifice for sins. Through the blood of Christ we have:</p>
    <ol>
      <li><span>01.</span>Remission of sins. Matthew 26:28 Heb 9:22</li>
      <li><span>02.</span>Sanctification. Hebrews 13:12</li>
      <li><span>03.</span>Redemption. Revelations 5:9</li>
      <li><span>04.</span>Cleansing. 1 John 1:7 Rev. 1:5</li>
      <li><span>05.</span>Justification. Romans 5:9</li>
    </ol>
  </div>
  <div class="art-div" style="left:479px;top:2795px"></div>
  <div class="art" style="left:479px;top:2838px">
    <h3>SECOND COMING OF CHRIST.</h3>
    <p>We believe in the second coming of Jesus Christ. Matthew 24:44 Luke 12:40</p>
  </div>
  <div class="art-div" style="left:479px;top:2990px"></div>

  <div class="art" style="left:791px;top:2413px">
    <h3>SANCTIFICATION</h3>
    <p>“Sanctify them through thy truth thy word is truth St John 17:17. For this is the will of God even your sanctification”</p>
    <p>We believe in a set apart life, separate from the world to Christ 2 Cor 6:17-18</p>
  </div>
  <div class="art-div" style="left:791px;top:2614px"></div>
  <div class="art" style="left:791px;top:2668px">
    <h3>DIVINE HEALING.</h3>
    <p>We believe Divine Healing to be included in the atonement of Jesus Christ our Lord, And believe that it is still for us today. 1 Peter 2:24 Luke 9:1-2 Mark 16-18 James 5:15</p>
  </div>
  <div class="art-div" style="left:791px;top:2828px"></div>
  <div class="art" style="left:791px;top:2878px">
    <h3>ETERNITY</h3>
    <p>We believe in Literal Eternity. Eternal Life for the believer and eternal death for those without Christ. Revelations 21:1-27</p>
  </div>

  <footer class="abs footer" style="top:3082px;height:403px">
    <div class="brand" style="left:141px;top:150px;width:280px;font-size:32px;letter-spacing:3px">GRACE<br>COVENANT</div>
    <p class="abs f-text" style="left:151px;top:234px;width:260px;text-align:center">Support our ministry through giving, prayer and serving.</p>
    <div class="btn" style="left:235px;top:279px;width:99px;height:35px">DONATE</div>

    <div class="abs f-title" style="left:594px;top:56px">CONTACT US</div>
    <div class="field" style="left:594px;top:100px;width:209px;height:34px">Name</div>
    <div class="field" style="left:814px;top:100px;width:208px;height:34px">Phone</div>
    <div class="field" style="left:594px;top:146px;width:428px;height:34px">Email address</div>
    <div class="field" style="left:594px;top:193px;width:428px;height:76px">Message</div>
    <div class="abs link-green" style="left:594px;top:286px">SEND US ⟶</div>

    <div class="abs copy" style="left:181px;top:366px">Copyright 2023 Grace Covenant Church I All rights reserved</div>
    <div class="abs social" style="left:921px;top:367px" aria-label="Social links"><span></span><span></span><span></span><span></span></div>
  </footer>

  <div class="abs variant">FOOTER 2 VARIANT</div>

  <footer class="abs footer" style="top:3548px;height:431px">
    <div class="brand" style="left:150px;top:152px;width:290px;font-size:36px;letter-spacing:3px">GRACE<br>COVENANT</div>

    <div class="abs f-title" style="left:471px;top:60px">CONTACT US</div>
    <div class="uline" style="left:471px;top:115px;width:252px"><span>Full Name:</span><span>◦</span></div>
    <div class="uline" style="left:471px;top:159px;width:252px"><span>Phone:</span><span>✆</span></div>
    <div class="uline" style="left:471px;top:203px;width:252px"><span>Email Address:</span><span>✉</span></div>
    <div class="uline" style="left:752px;top:115px;width:270px;height:110px"><span>Message</span><span>✎</span></div>
    <div class="abs link-green" style="left:471px;top:248px;width:108px;height:35px;border:1px solid var(--green);display:flex;align-items:center;justify-content:center;padding:0">SEND US ⟶</div>

    <p class="abs f-text" style="left:471px;top:319px">Support our ministry through giving, prayer and serving in our community.</p>
    <div class="btn" style="left:920px;top:311px;width:99px;height:35px">DONATE</div>

    <div class="abs copy" style="left:181px;top:388px">Copyright 2023 Grace Covenant Church I All rights reserved</div>
    <div class="abs social" style="left:921px;top:389px" aria-label="Social links"><span></span><span></span><span></span><span></span></div>
  </footer>

</div>
</body>
</html>
```